Advertising company unique advertising platform

we need a logo design for a new company based in Australia Melbourne. We develop innovated advertising platform where consumer can use this platform to get regular discount, as business owner they can use this platform for free advertisement. Payment for this advertisement platform only payable every two weeks, when I generate revenue for their business

Industry/Entity Type

Advertising

Contact Information for Business Card

Dale Morven | Co-Founder |Managing Director
Suite 718 240 Wattlebrook Lane Melbourne Vic 3000

ABN 38 614 207 923
Tel: +61 0487 259 318 | Email: dale.morven@plivorantu.com

Font styles to use
Decorative
Script

Requirements
Must have
• Try few different design and some round corner business card
Should not have
• One round corner business card...try 4 different colour background not only black, make sure two side is designed. Be creative so imagine you are giving this to a client make sure has wow factor, if you can also try one design with engrave like all the logo, words look 3d feel
• The word Advertising Platform use attached file font

```html
<!DOCTYPE html>
<html lang="en">
<head>
<meta charset="utf-8">
<title>Plivorantu – Business Card</title>
<link rel="stylesheet" href="https://fonts.googleapis.com/css2?family=Open+Sans:wght@400;600;700&display=swap">
<style>
  :root {
    --stage: #e9e7e4;
    --card: #17181a;
    --card-edge: #222326;
    --name: #e8542c;
    --title: #2fd3a8;
    --ink: #f2f2f2;
    --muted: #8d8f93;
    --rule: #d9d9d9;
    --brand: #ef7a32;
  }
  * { margin: 0; padding: 0; box-sizing: border-box; }
  html, body { width: 1200px; height: 864px; overflow: hidden; }
  body {
    background: var(--stage);
    font-family: "Open Sans", Arial, sans-serif;
    display: flex;
    align-items: center;
    justify-content: center;
    gap: 40px;
  }
  .card {
    position: relative;
    width: 540px;
    height: 309px;
    background: var(--card);
    border: 1px solid var(--card-edge);
    box-shadow: 0 10px 28px rgba(0,0,0,0.25);
    color: var(--ink);
  }

  /* Back side */
  .card-back { display: flex; flex-direction: column; align-items: center; justify-content: center; gap: 26px; }
  .back-brand { display: flex; align-items: center; gap: 12px; }
  .brand-dot { width: 22px; height: 22px; border-radius: 50%; background: var(--brand); }
  .back-brand .brand-name { font-size: 30px; font-weight: 700; color: var(--brand); }
  .website { font-size: 13px; letter-spacing: 4px; color: var(--muted); }

  /* Front side */
  .holder { position: absolute; left: 34px; top: 44px; }
  .holder-name { font-size: 17px; font-weight: 700; color: var(--name); letter-spacing: 0.3px; text-transform: uppercase; }
  .holder-title { font-size: 14px; font-weight: 400; color: var(--title); text-transform: uppercase; line-height: 1.25; }
  .rule { position: absolute; height: 1px; background: var(--rule); }
  .rule-top { left: 34px; top: 120px; width: 300px; }
  .rule-bottom { left: 260px; top: 210px; width: 246px; }
  .contact { position: absolute; left: 34px; top: 134px; list-style: none; font-size: 13px; line-height: 1.5; }
  .contact li { display: flex; align-items: center; gap: 8px; }
  .contact .icon { width: 11px; height: 11px; fill: var(--name); flex: none; }
  .front-brand { position: absolute; right: 34px; top: 142px; display: flex; align-items: center; gap: 10px; }
  .front-brand .brand-dot { width: 16px; height: 16px; }
  .front-brand .brand-name { font-size: 24px; font-weight: 700; color: var(--brand); }
  .address { position: absolute; right: 34px; bottom: 30px; text-align: right; font-size: 14px; line-height: 1.35; font-style: normal; }
</style>
</head>
<body>
  <section class="card card-back">
    <div class="back-brand">
      <span class="brand-dot"></span>
      <span class="brand-name">Kestrelle Loop</span>
    </div>
    <p class="website">www.plivorantu.com</p>
  </section>

  <section class="card card-front">
    <div class="holder">
      <p class="holder-name">Dale Morven</p>
      <p class="holder-title">Co-Founder</p>
      <p class="holder-title">Managing Director</p>
    </div>
    <div class="rule rule-top"></div>
    <ul class="contact">
      <li>
        <svg class="icon" viewBox="0 0 12 12" aria-hidden="true"><path d="M2.5 0.5 L4.5 0.5 L5.2 3 L3.8 4.2 Q5 7 7.8 8.2 L9 6.8 L11.5 7.5 L11.5 9.5 Q11.5 11.5 9.5 11.5 Q0.5 10.5 0.5 2.5 Q0.5 0.5 2.5 0.5 Z"/></svg>
        +61 0487 259 318
      </li>
      <li>
        <svg class="icon" viewBox="0 0 12 12" aria-hidden="true"><path d="M0.5 2 H11.5 V10 H0.5 Z M1 2.5 L6 6.5 L11 2.5" /></svg>
        dale.morven@plivorantu.com
      </li>
      <li>Plivorantu</li>
      <li>ABN 38 614 207 923</li>
    </ul>
    <div class="front-brand">
      <span class="brand-dot"></span>
      <span class="brand-name">Kestrelle Loop</span>
    </div>
    <div class="rule rule-bottom"></div>
    <address class="address">
      Suite 718 240 Wattlebrook<br>
      Lane<br>
      Melbourne Vic 3000
    </address>
  </section>
</body>
</html>
```